Flyer for spiritual retreat (yoga, meditation, reiki, raw food)

I would like a flyer to promote my upcoming retreat and a matching Facebook banner.

The name of the retreat is "OutBloom the Spirit" and the tagline is "retreat into you"

The activities in the retreat include daily meditation, ecstatic dance, spiritual development workshops on intuition, energy healing etc and a reiki session is included.

I would like a flyer designed to promote this, something that is editable as I will be running this multiple times and will need to adjust the flyer to add the dates etc each time.

edit: add that here will be fully catered raw food and juices, and that the retreat price includes all accomodation, meals and workshops.

Please contact me if you need further info. Please also visit my website www.marlavosk.com and www.pagenest.com/koruhaven to see my current events and promotions.

Thank you,

Marla

Reason: Hi all, thank you all for your submissions. Apologies as I am traveling and do not have much access to internet and will review your submissions and provide feedback as soon as possible. Kind regards, Marla.

Target Market(s)

People who like meditation, yoga, fans of tomas brenner and wendell marsh, those interested in personal and spiritual development.

Industry/Entity Type

Health And Wellness

Requirements
Must have
• Please put the included reiki session as as added bonus. Something like "BONUS 30 minute reiki healing session" in a little star/banner/something that stands out.
• Please emphasise the "light" part of OutBloom as I am going for a play on words between in the light and enlightenment.
• Please include placeholder text for place, location, time
• Placeholder for price
• My name (see attached file - can change colour to suit) and website (www.marlavosk.com)
Nice to have
• I prefer rounded designs, curves rather than block designs.
Should not have
• Koru Haven logo

```html
<!DOCTYPE html>
<html lang="en">
<head>
<meta charset="utf-8">
<title>OutBloom the Spirit – Retreat Flyer</title>
<link rel="stylesheet" href="https://fonts.googleapis.com/css2?family=Oswald:wght@500;700&family=Lobster&family=Great+Vibes&family=Roboto:ital,wght@0,400;0,700;1,400;1,700&display=swap">
<style>
  :root {
    --blue: #0aaee9;
    --blue-light: #4fd0ff;
    --blue-deep: #0a8fcf;
    --ink: #1e1f21;
    --charcoal: #2b2c2e;
    --paper: #f4f4f4;
    --ring: #e3e3e3;
    --text: #1a1a1a;
    --page: #e9eaec;
  }
  * { box-sizing: border-box; margin: 0; padding: 0; }
  html, body { width: 1200px; height: 1200px; overflow: hidden; background: var(--page); }
  .flyer {
    position: absolute; left: 202px; top: 37px;
    width: 885px; height: 1251px;
    transform: scale(0.9); transform-origin: top left;
    background: var(--paper); overflow: hidden;
    box-shadow: 0 10px 40px rgba(0,0,0,.25);
    font-family: "Roboto", Arial, sans-serif;
  }
  .layer { position: absolute; left: 0; top: 0; width: 885px; height: 1251px; }
  .tagline {
    position: absolute; left: 45px; top: 52px;
    font-family: "Lobster", cursive; font-size: 72px; color: var(--blue);
    -webkit-text-stroke: 2px #fff; letter-spacing: -1px;
    text-shadow: 0 0 4px rgba(255,255,255,.9), 0 3px 6px rgba(0,0,0,.15);
    transform: rotate(-2deg); white-space: nowrap;
  }
  .host-name {
    position: absolute; left: 570px; top: 82px;
    font-family: "Great Vibes", cursive; font-size: 64px; line-height: 1; color: #fff;
    white-space: nowrap;
    text-shadow: 0 0 8px rgba(255,255,255,.5);
  }
  .photo-circle {
    position: absolute; border-radius: 50%;
    border: 4px solid var(--blue);
    box-shadow: 0 0 0 14px var(--ring), 0 6px 16px 14px rgba(0,0,0,.12);
  }
  .photo-host { left: 530px; top: 213px; width: 300px; height: 300px;
    background: linear-gradient(120deg, #7fa86a 0%, #b8cfae 35%, #cfa992 60%, #4a3b35 100%); }
  .photo-pose { left: 395px; top: 498px; width: 250px; height: 250px;
    background: linear-gradient(180deg, #ffffff 0%, #f2efec 60%, #dcdfe6 100%); }
  .photo-sky { left: 619px; top: 517px; width: 192px; height: 192px;
    background: linear-gradient(180deg, #b7cde6 0%, #e9f1fa 55%, #c9dce6 100%); }
  .headline { position: absolute; font-family: "Oswald", sans-serif; font-weight: 700; font-style: italic; letter-spacing: -1px; line-height: 1; white-space: nowrap; }
  .headline-one { left: 35px; top: 722px; font-size: 82px; color: var(--ink); }
  .headline-one .light { color: #fff; text-shadow: 0 2px 4px rgba(0,0,0,.25); }
  .headline-two { left: 215px; top: 800px; font-size: 82px; color: #fff; text-shadow: 0 2px 4px rgba(0,0,0,.25); }
  .price { position: absolute; right: 28px; top: 775px; text-align: right; font-family: "Oswald", sans-serif; font-weight: 700; font-style: italic; line-height: 1; }
  .price-label { font-size: 50px; color: var(--ink); }
  .price-value { font-size: 68px; color: var(--blue); text-shadow: 0 2px 3px rgba(0,0,0,.15); }
  .bonus { position: absolute; left: 632px; top: 900px; width: 253px; height: 95px; }
  .bonus-text { position: absolute; right: 32px; top: 16px; text-align: right; font-family: "Oswald", sans-serif; font-weight: 700; font-style: italic; line-height: 1.15; white-space: nowrap; }
  .bonus-title { font-size: 27px; color: var(--blue); }
  .bonus-sub { font-size: 22px; color: #fff; }
  .divider { position: absolute; left: 575px; top: 885px; width: 8px; height: 310px; background: var(--blue); }
  .cta {
    position: absolute; left: 47px; top: 993px; width: 440px; height: 55px;
    border-radius: 28px; background: linear-gradient(180deg, var(--blue-light), var(--blue) 60%, var(--blue-deep));
    box-shadow: 0 10px 12px -6px rgba(0,0,0,.3);
    font-family: "Oswald", sans-serif; font-weight: 700; font-style: italic; font-size: 33px; color: #fff;
    display: flex; align-items: center; justify-content: center; white-space: nowrap;
  }
  .details { position: absolute; left: 46px; top: 1086px; font-size: 15px; font-weight: 700; font-style: italic; color: var(--text); white-space: nowrap; }
  .details .blank { display: inline-block; border-bottom: 1px solid var(--text); margin-right: 6px; height: 12px; }
  .note { position: absolute; left: 41px; top: 1126px; width: 500px; font-size: 15px; font-style: italic; line-height: 1.33; color: var(--text); }
  .activities-title { position: absolute; right: 44px; top: 1016px; font-size: 18px; font-style: italic; color: var(--blue); white-space: nowrap; }
  .activities { position: absolute; right: 70px; top: 1048px; text-align: right; list-style: none; font-size: 15px; font-style: italic; color: var(--text); }
  .activities li { position: relative; margin-bottom: 6px; line-height: 1.3; white-space: nowrap; }
  .activities li::after { content: ""; position: absolute; right: -22px; top: 5px; width: 11px; height: 11px; border-radius: 50%; background: var(--blue); }
  .footer { position: absolute; left: 0; top: 1192px; width: 885px; height: 59px; background: var(--blue); display: flex; align-items: center; font-size: 16px; letter-spacing: 1px; color: #fff; font-style: italic; white-space: nowrap; }
  .footer-label { width: 358px; height: 100%; margin-top: 8px; background: var(--charcoal); display: flex; align-items: center; justify-content: center; padding-bottom: 8px; }
  .footer-links { padding-left: 20px; margin-top: 6px; }
</style>
</head>
<body>
<main class="flyer">
  <svg class="layer" viewBox="0 0 885 1251" role="img" aria-label="Photo of a woman meditating cross-legged on a sunny beach by the sea">
    <defs>
      <linearGradient id="beach" x1="0" y1="0" x2="0" y2="1">
        <stop offset="0" stop-color="#dff1fb"/>
        <stop offset="0.35" stop-color="#f7fbfd"/>
        <stop offset="0.5" stop-color="#a9c7d6"/>
        <stop offset="0.65" stop-color="#eef3f5"/>
        <stop offset="1" stop-color="#d9d3cb"/>
      </linearGradient>
    </defs>
    <rect x="0" y="0" width="620" height="760" fill="url(#beach)"/>
  </svg>

  <svg class="layer" viewBox="0 0 885 1251" aria-hidden="true">
    <defs>
      <linearGradient id="swoosh" x1="0" y1="0" x2="1" y2="1">
        <stop offset="0" stop-color="#08a6e4"/>
        <stop offset="0.5" stop-color="#12b8f2"/>
        <stop offset="1" stop-color="#0a9fdd"/>
      </linearGradient>
    </defs>
    <path d="M478,0 H885 V400 C800,430 620,420 520,400 C500,300 545,120 478,0 Z" fill="var(--blue)"/>
    <path d="M505,0 H885 V390 C800,420 640,410 545,395 C525,300 570,120 505,0 Z" fill="var(--charcoal)"/>
    <path d="M0,640 C200,700 420,690 560,640 L885,320 V605 C720,860 380,985 0,905 Z" fill="var(--ink)"/>
    <path d="M0,640 C200,700 420,690 560,640 L885,320 V590 C720,840 380,965 0,890 Z" fill="url(#swoosh)"/>
    <path d="M330,690 C450,690 560,650 640,560 C560,720 460,800 330,690 Z" fill="#fff" opacity=".12"/>
  </svg>

  <div class="tagline">Retreat into you</div>
  <div class="host-name">Marla Vosk</div>

  <div class="photo-circle photo-host" role="img" aria-label="Portrait of the retreat host smiling outdoors"></div>
  <div class="photo-circle photo-pose" role="img" aria-label="Woman in white holding a kneeling yoga pose"></div>
  <div class="photo-circle photo-sky" role="img" aria-label="Woman seen from behind with arms open toward a bright sky"></div>

  <h1>
    <span class="headline headline-one">Out<span class="light">Bloom</span></span>
    <span class="headline headline-two">the Spirit</span>
  </h1>

  <div class="price">
    <div class="price-label">Price</div>
    <div class="price-value">$00</div>
  </div>

  <div class="bonus">
    <svg width="253" height="95" viewBox="0 0 253 95" aria-hidden="true">
      <path d="M20,0 H253 V95 H20 L0,47 Z" fill="var(--blue)"/>
      <path d="M36,0 H253 V95 H36 L16,47 Z" fill="var(--charcoal)"/>
    </svg>
    <div class="bonus-text">
      <div class="bonus-title">BONUS 30 minute</div>
      <div class="bonus-sub">reiki healing session</div>
    </div>
  </div>

  <div class="divider"></div>

  <div class="cta">Join Our Upcoming Retreat</div>

  <p class="details">
    Place:<span class="blank" style="width:98px"></span>
    Location:<span class="blank" style="width:108px"></span>
    Time:<span class="blank" style="width:116px"></span>
  </p>
  <p class="note">Retreat will have fully catered raw food and juices. The retreat price includes all accomodation, meals and workshops.</p>

  <h2 class="activities-title">The Retreat Activities:</h2>
  <ul class="activities">
    <li>Daily meditation</li>
    <li>Ecstatic dance</li>
    <li>Spiritual development<br>workshops on intuition</li>
    <li>Energy healing</li>
    <li>A reiki session</li>
  </ul>

  <footer class="footer">
    <div class="footer-label">For further info please visit us at:</div>
    <div class="footer-links">www.marlavosk.com &nbsp;|&nbsp; www.pagenest.com/koruhaven</div>
  </footer>
</main>
</body>
</html>
```